Inspiring Fundraising Foundation Website to Provide Academic Scholarships

Hello, we are launching a foundation to provide academic scholarships to high school students for college. We'd like this to be an informational website with contact information. There will be a total of approximately 5-7 pages in all.
The color scheme will be purple and white, with a girly feel. I 've attached the logo for reference!

Target Market(s)

high school students, college students

Industry/Entity Type

Education

Coding

Coded - Design and coding required

Number of Pages Required

5+ page

Font styles to use
Serif
Sans Serif
Script

Colors
6b449b
886aae
b7a5cd
e4daeb
ffffff
fdf9cf
fbf289

Requirements
Must have
• Purple, girly feel, to reflect the logo's style. Should be light-themed
Should not have
• No dark themes (aka heavy on black or dark colors)

```html
<!DOCTYPE html>
<html lang="en">
<head>
<meta charset="utf-8">
<title>Lorelei Vance Foundation</title>
<link href="https://fonts.googleapis.com/css2?family=Open+Sans:ital,wght@0,300;0,400;0,600;0,700;1,400&display=swap" rel="stylesheet">
<style>
:root{
  --purple:#6b449b;
  --purple-mid:#886aae;
  --purple-soft:#b7a5cd;
  --lilac:#e4daeb;
  --plum:#3b1356;
  --yellow:#fbf289;
  --cream:#fdf9cf;
  --white:#ffffff;
  --grey-bg:#f7f7f7;
  --text:#555555;
  --line:#e3e3e3;
}
*{margin:0;padding:0;box-sizing:border-box}
html,body{width:1200px;height:2946px;overflow:hidden}
body{font-family:"Open Sans",Arial,sans-serif;color:var(--text);background:var(--white);position:relative}
section,header,footer{position:relative;width:1200px}
.btn{display:inline-block;text-transform:uppercase;font-size:15px;text-align:center;text-decoration:none}
.btn-yellow{background:var(--yellow);color:var(--plum)}
.btn-plum{background:var(--plum);color:var(--white)}
.section-title{font-weight:400;color:var(--plum);text-align:center;text-transform:uppercase;font-size:37px;letter-spacing:.5px}

/* Hero */
.hero{height:515px;overflow:hidden}
.hero-photo{position:absolute;inset:0;background:linear-gradient(120deg,#7a5a8e 0%,#8a5f93 35%,#6d4a86 65%,#5d3f7a 100%)}
.hero-tint{position:absolute;inset:0;background:rgba(107,68,155,.55)}
.nav{position:absolute;top:62px;left:0;width:1200px;height:24px}
.nav a{position:absolute;color:var(--white);font-size:14px;text-decoration:none;text-transform:uppercase}
.nav-brand{position:absolute;left:520px;top:60px;width:160px;text-align:center;color:var(--white);font-size:17px;font-weight:600;line-height:22px}
.hero-title{position:absolute;top:245px;width:1200px;text-align:center;color:var(--white);font-size:37px;font-weight:400;text-transform:uppercase}
.hero-sub{position:absolute;top:303px;width:1200px;text-align:center;color:var(--white);font-size:15px;letter-spacing:2px}
.hero .btn{position:absolute;left:509px;top:355px;width:182px;height:50px;line-height:50px}
.dots{position:absolute;top:465px;left:572px;display:flex;gap:7px}
.dots span{width:8px;height:8px;border-radius:50%;background:var(--white)}

/* About */
.about{height:412px}
.about-photo{position:absolute;left:0;top:0;width:463px;height:412px;background:linear-gradient(180deg,#eeeeee 0%,#e2d6d4 50%,#b8413a 80%,#9f332e 100%)}
.about h2{position:absolute;left:501px;top:90px;font-size:37px;font-weight:400;color:var(--plum);text-transform:uppercase}
.about p{position:absolute;left:499px;top:172px;width:505px;font-size:14.5px;line-height:29px;color:var(--text)}
.about .btn{position:absolute;left:497px;top:318px;width:134px;height:36px;line-height:36px;font-size:14px}

/* Scholarships */
.scholarships{height:581px;background:var(--grey-bg)}
.scholarships .section-title{position:absolute;top:116px;width:1200px}
.scholar-card{position:absolute;top:212px;width:289px}
.campus{height:165px}
.campus-1{background:linear-gradient(135deg,#c79b5f 0%,#f2d79a 45%,#b7a35e 100%)}
.campus-2{background:linear-gradient(180deg,#8cb3d6 0%,#a2603f 50%,#6d8a4a 100%)}
.campus-3{background:linear-gradient(180deg,#a9cbe6 0%,#9b4634 50%,#6e9a42 100%)}
.person{display:flex;align-items:center;margin-top:22px}
.avatar{width:64px;height:64px;border-radius:50%;background:linear-gradient(180deg,#d9c7bf,#8a6a5d);border:3px solid var(--white);flex:none}
.person-info{margin-left:18px;font-size:11px;line-height:16px;color:#555}
.person-info strong{display:block;color:var(--plum);font-weight:600;font-size:12px}
.person-info em{display:block}

/* News */
.news{height:566px}
.news .section-title{position:absolute;top:68px;width:1200px}
.news-item{position:absolute;top:165px;width:450px}
.date-box{position:absolute;left:0;top:0;width:130px;height:116px;background:var(--yellow);text-align:center;color:#6f6452;padding-top:20px;line-height:23px}
.date-box .mon{display:block;font-size:29px;font-weight:700}
.date-box .day{display:block;font-size:23px}
.news-item h3{position:absolute;left:146px;top:2px;width:300px;font-size:25px;font-weight:400;line-height:36px;color:#555}
.news-item p{position:absolute;left:0;top:154px;width:445px;font-size:14px;line-height:29px;color:#666}
.news-item .btn{position:absolute;left:0;top:267px;width:136px;height:37px;line-height:37px;font-size:14px}

/* Testimonials */
.testimonials{height:511px;background:var(--grey-bg)}
.testimonials .section-title{position:absolute;top:62px;width:1200px}
.testimonial{position:absolute;top:176px;width:289px}
.quote-box{position:relative;height:142px;background:var(--white);border:1px solid var(--line);padding:22px 10px 0 60px;font-size:10px;line-height:24px;color:#555}
.quote-box .mark{position:absolute;left:10px;top:10px;font-family:Georgia,serif;font-size:62px;line-height:60px;color:var(--plum);font-weight:700}
.quote-box::after{content:"";position:absolute;left:64px;bottom:-11px;width:20px;height:20px;background:var(--white);border-right:1px solid var(--line);border-bottom:1px solid var(--line);transform:rotate(45deg)}
.quote-text{display:block;height:96px;overflow:hidden}
.testimonial .person{margin-top:26px;margin-left:28px}

/* Footer */
.footer{height:294px;border-bottom:1px solid var(--line)}
.footer-brand{position:absolute;left:142px;top:72px;width:100px;color:var(--purple);font-size:21px;font-weight:600;line-height:26px}
.footer-col{position:absolute;top:47px}
.footer-col h4{font-size:11.5px;font-weight:700;color:var(--plum);text-transform:uppercase;margin-bottom:25px}
.footer-col a{display:block;color:#444;font-size:12px;line-height:29px;text-decoration:none}
.socials{display:flex;gap:14px;margin-top:4px}
.socials span{width:12px;height:12px;border-radius:50%;background:var(--plum)}
.copyright{position:absolute;top:2893px;width:1200px;text-align:center;font-size:11.5px;color:#444;text-transform:uppercase}
</style>
</head>
<body>

<header class="hero">
  <div class="hero-photo" role="img" aria-label="Photo of smiling children in a classroom"></div>
  <div class="hero-tint"></div>
  <nav class="nav">
    <a href="#" style="left:182px">Home</a>
    <a href="#" style="left:274px">About Us</a>
    <a href="#" style="left:392px">Scholarship</a>
    <a href="#" style="left:672px">Students</a>
    <a href="#" style="left:794px">Members</a>
    <a href="#" style="left:910px">Contact Us</a>
  </nav>
  <div class="nav-brand">Lorelei Vance</div>
  <h1 class="hero-title">Lorelei Vance Foundation</h1>
  <p class="hero-sub">A Fundraising Foundation</p>
  <a class="btn btn-yellow" href="#">Learn More</a>
  <div class="dots"><span></span><span></span><span></span><span></span></div>
</header>

<section class="about">
  <div class="about-photo" role="img" aria-label="Portrait of the foundation's namesake seated on a red sofa"></div>
  <h2>Lorelei Vance</h2>
  <p>We are excited to announce the Lorelei Vance Foundation in honor of a fabulous angel. We hope to impact the lives of individuals in the same way her dynamic spirit impacted ours. Lorelei, we love you and miss you everyday, and through this foundation your name will live on.</p>
  <a class="btn btn-yellow" href="#">Read More</a>
</section>

<section class="scholarships">
  <h2 class="section-title">Academic Scholarships</h2>
  <article class="scholar-card" style="left:141px">
    <div class="campus campus-1" role="img" aria-label="Photo of a brick school building at sunrise"></div>
    <div class="person"><div class="avatar" role="img" aria-label="Student portrait"></div>
      <div class="person-info"><strong>Daniel Hart</strong><em>Oakridge Matriculation School</em>Standard : IX-D Grade</div></div>
  </article>
  <article class="scholar-card" style="left:454px">
    <div class="campus campus-2" role="img" aria-label="Photo of a modern brick campus building"></div>
    <div class="person"><div class="avatar" role="img" aria-label="Student portrait"></div>
      <div class="person-info"><strong>Daniel Hart</strong><em>Oakridge Matriculation School</em>Standard : IX-D Grade</div></div>
  </article>
  <article class="scholar-card" style="left:764px">
    <div class="campus campus-3" role="img" aria-label="Photo of a red brick college hall with gardens"></div>
    <div class="person"><div class="avatar" role="img" aria-label="Student portrait"></div>
      <div class="person-info"><strong>Daniel Hart</strong><em>Oakridge Matriculation School</em>Standard : IX-D Grade</div></div>
  </article>
</section>

<section class="news">
  <h2 class="section-title">News</h2>
  <article class="news-item" style="left:141px">
    <div class="date-box"><span class="mon">FEB</span><span class="day">17TH</span><span class="day">2017</span></div>
    <h3>Lorem ipsum dolor sit amet, consectetur adipiscing elit</h3>
    <p>Lorem ipsum dolor sit amet, consectetur adipiscing elit, sed do eiusmod tempor incididunt ut labore et dolore magna aliqua. Ut enim ad minim veniam, quis nostrud exercitation</p>
    <a class="btn btn-plum" href="#">Read More</a>
  </article>
  <article class="news-item" style="left:611px">
    <div class="date-box"><span class="mon">FEB</span><span class="day">17TH</span><span class="day">2017</span></div>
    <h3>Lorem ipsum dolor sit amet, consectetur adipiscing elit</h3>
    <p>Lorem ipsum dolor sit amet, consectetur adipiscing elit, sed do eiusmod tempor incididunt ut labore et dolore magna aliqua. Ut enim ad minim veniam, quis nostrud exercitation</p>
    <a class="btn btn-plum" href="#">Read More</a>
  </article>
</section>

<section class="testimonials">
  <h2 class="section-title">Testimonials</h2>
  <article class="testimonial" style="left:141px">
    <div class="quote-box"><span class="mark">&ldquo;</span><span class="quote-text">Lorem ipsum dolor sit amet, consectetur adipiscing elit, sed do eiusmod tempor incididunt ut labore et dolore magna aliqua. Ut enim ad minim veniam</span></div>
    <div class="person"><div class="avatar" role="img" aria-label="Student portrait"></div>
      <div class="person-info"><strong>Daniel Hart</strong><em>Oakridge Matriculation School</em></div></div>
  </article>
  <article class="testimonial" style="left:454px">
    <div class="quote-box"><span class="mark">&ldquo;</span><span class="quote-text">Lorem ipsum dolor sit amet, consectetur adipiscing elit, sed do eiusmod tempor incididunt ut labore et dolore magna aliqua. Ut enim ad minim veniam</span></div>
    <div class="person"><div class="avatar" role="img" aria-label="Student portrait"></div>
      <div class="person-info"><strong>Daniel Hart</strong><em>Oakridge Matriculation School</em></div></div>
  </article>
  <article class="testimonial" style="left:764px">
    <div class="quote-box"><span class="mark">&ldquo;</span><span class="quote-text">Lorem ipsum dolor sit amet, consectetur adipiscing elit, sed do eiusmod tempor incididunt ut labore et dolore magna aliqua. Ut enim ad minim veniam</span></div>
    <div class="person"><div class="avatar" role="img" aria-label="Student portrait"></div>
      <div class="person-info"><strong>Daniel Hart</strong><em>Oakridge Matriculation School</em></div></div>
  </article>
</section>

<footer class="footer">
  <div class="footer-brand">Lorelei Vance</div>
  <div class="footer-col" style="left:373px">
    <h4>Quick Links</h4>
    <a href="#">Home</a><a href="#">About Us</a><a href="#">Scholarship</a><a href="#">Students</a><a href="#">Members</a><a href="#">Contact Us</a>
  </div>
  <div class="footer-col" style="left:609px">
    <h4>Other Links</h4>
    <a href="#">Terms Of Service</a><a href="#">Privacy Policy</a><a href="#">Help</a><a href="#">Disclaimer</a>
  </div>
  <div class="footer-col" style="left:845px">
    <h4>Connect With Us</h4>
    <div class="socials"><span></span><span></span><span></span><span></span><span></span></div>
  </div>
</footer>
<p class="copyright">&copy; 2017 Company Name &nbsp;|&nbsp; All Rights Reserved</p>

</body>
</html>
```